MRT Property - Business Cards

Looking for a business card & general letterhead, signage etc design for our new logo.

Colours:
000a20
0056a2
00b5ef
0088ce
68cef2

Fonts:
Poppins
Karla

Please keep look and feel of new brand - example in the zip package I sent.

```html
<!DOCTYPE html>
<html lang="en">
<head>
<meta charset="utf-8">
<title>MRT Property – Business Cards</title>
<link rel="stylesheet" href="https://fonts.googleapis.com/css2?family=Poppins:wght@400;500;600;700&family=Karla:wght@400;500&display=swap">
<style>
  :root {
    --ink-navy: #000a20;
    --card-navy: #161a30;
    --brand-blue: #0056a2;
    --brand-cyan: #00b5ef;
    --brand-mid: #0088ce;
    --brand-light: #68cef2;
    --paper: #f7f8fa;
    --text-grey: #3b3f4a;
    --backdrop: #1b1b1d;
  }
  * { margin: 0; padding: 0; box-sizing: border-box; }
  html, body {
    width: 1200px; height: 852px; overflow: hidden;
    background: var(--backdrop);
    font-family: "Poppins", sans-serif;
  }
  .sheet {
    position: relative; width: 1200px; height: 852px;
    display: flex; align-items: center; justify-content: center; gap: 40px;
  }
  .card {
    position: relative; width: 520px; height: 300px;
    border-radius: 18px; overflow: hidden;
  }

  /* Front (dark) */
  .card--front { background: var(--card-navy); }
  .card--front .brand-name {
    position: absolute; left: 0; right: 0; top: 104px;
    text-align: center;
    font-family: "Poppins", sans-serif; font-weight: 700;
    font-size: 44px; letter-spacing: 1px;
    color: var(--brand-mid);
  }
  .card--front .web {
    position: absolute; right: 26px; bottom: 38px;
    font-family: "Karla", sans-serif; font-size: 11px;
    letter-spacing: 5px; color: #c9ccd8;
  }
  .card--front .rule {
    position: absolute; left: 0; right: 0; bottom: 22px; height: 4px;
    background: linear-gradient(90deg, var(--brand-blue) 0 55%, var(--brand-cyan) 55% 100%);
  }

  /* Back (white) */
  .card--back { background: var(--paper); }
  .card--back .brand-name {
    position: absolute; left: 34px; top: 40px;
    font-family: "Poppins", sans-serif; font-weight: 700;
    font-size: 34px; color: var(--brand-mid);
  }
  .holder { position: absolute; left: 34px; top: 128px; }
  .holder .name {
    font-weight: 600; font-size: 20px; color: var(--brand-mid); line-height: 1.1;
  }
  .holder .role {
    font-family: "Karla", sans-serif; font-size: 10px; color: var(--text-grey);
    margin-top: 3px;
  }
  .contacts {
    position: absolute; left: 34px; top: 190px; list-style: none;
    font-family: "Karla", sans-serif; font-size: 13px; color: var(--text-grey);
  }
  .contacts li { display: flex; align-items: center; gap: 12px; height: 20px; }
  .contacts svg { width: 12px; height: 12px; fill: var(--brand-blue); flex: none; }
  .footer-band { position: absolute; left: 0; bottom: 0; width: 520px; height: 110px; }
  .address {
    position: absolute; right: 22px; bottom: 74px;
    font-family: "Karla", sans-serif; font-size: 12px; color: #ffffff;
  }
</style>
</head>
<body>
<main class="sheet">

  <section class="card card--front" aria-label="Business card front">
    <div class="brand-name">MRT Property</div>
    <div class="web">www.mrtproperty.com</div>
    <div class="rule"></div>
  </section>

  <section class="card card--back" aria-label="Business card back">
    <div class="brand-name">MRT Property</div>

    <div class="holder">
      <div class="name">Daniel Moore</div>
      <div class="role">Associate Director</div>
    </div>

    <ul class="contacts">
      <li>
        <svg viewBox="0 0 24 24" aria-hidden="true"><path d="M6.6 10.8a15 15 0 0 0 6.6 6.6l2.2-2.2a1 1 0 0 1 1-.25 11.4 11.4 0 0 0 3.6.57 1 1 0 0 1 1 1V20a1 1 0 0 1-1 1A17 17 0 0 1 3 4a1 1 0 0 1 1-1h3.5a1 1 0 0 1 1 1c0 1.25.2 2.45.57 3.57a1 1 0 0 1-.25 1z"/></svg>
        555-010-0199
      </li>
      <li>
        <svg viewBox="0 0 24 24" aria-hidden="true"><path d="M2 5h20v14H2z M3 6l9 7 9-7" fill="none" stroke="#0056a2" stroke-width="2.4"/></svg>
        info@mrtproperty.com
      </li>
      <li>
        <svg viewBox="0 0 24 24" aria-hidden="true"><circle cx="12" cy="12" r="9" fill="none" stroke="#0056a2" stroke-width="2.4"/><path d="M3 12h18M12 3c-3 3-3 15 0 18M12 3c3 3 3 15 0 18" fill="none" stroke="#0056a2" stroke-width="1.8"/></svg>
        www.mrtproperty.com
      </li>
    </ul>

    <svg class="footer-band" viewBox="0 0 520 110" aria-hidden="true">
      <path d="M0 96 L290 96 C300 96 304 90 306 84 L330 22 C333 15 338 12 346 12 L520 12 L520 110 L0 110 Z" fill="var(--brand-cyan)"/>
      <path d="M0 102 L280 102 C292 102 300 96 304 88 L330 20 C333 13 338 10 346 10 L520 10 L520 110 L0 110 Z" fill="var(--paper)" opacity="0"/>
      <path d="M310 110 L330 22 C333 15 338 12 346 12 L520 12 L520 110 Z" fill="var(--brand-blue)"/>
    </svg>
    <div class="address">27 Harbour View Road Northmead</div>
  </section>

</main>
</body>
</html>
```